Business Card Design Project

This is the first time we use our new logo. We need a business card that we can use both on our institutional corporate relationships and also that works for our staff that deals with consumers directly.

VELUNDA is a new company dedicated to empower consumers and to provide them with the best choices for specialized health care using the latest telemedicine technology (medicine at a distance via videoconference).

We want to print this cards in high quality materials and process. We will like designs that allow us to use UV spot varnish and other techniques that will differentiate us.

We are including Two different versions of Color logos. In addition we are including white over black background logos. Those can be used replacing the black for a color.

Please note this is the first time we will be creating any corporate materials with our new logo and colors.

Target Market(s)

34+ consumers of medium high and high socioeconomic levels.

Industry/Entity Type

Health

Requirements
Must have
• Our logo on its original colors
Should not have
• Any other graphical element or design that is not our logo

```html
<!DOCTYPE html>
<html lang="en">
<head>
<meta charset="utf-8">
<title>VELUNDA Business Card</title>
<link rel="stylesheet" href="https://fonts.googleapis.com/css2?family=Montserrat:wght@500;600;700&display=swap">
<style>
  :root {
    --page: #e9e6e2;
    --card-dark: #1b1b1d;
    --card-mid: #2b2b2e;
    --band: #5bb6df;
    --rule: #14a39a;
    --brand-blue: #1f6ba6;
    --accent-teal: #14a8a0;
    --text-light: #f2f2f2;
    --divider: #8a8a8a;
  }
  html, body {
    margin: 0;
    width: 1200px;
    height: 1057px;
    overflow: hidden;
    background: var(--page);
    font-family: "Montserrat", Arial, sans-serif;
  }
  .sheet {
    position: relative;
    width: 1200px;
    height: 1057px;
  }
  .card {
    position: absolute;
    left: 170px;
    width: 860px;
    height: 491px;
    background:
      repeating-linear-gradient(0deg, rgba(255,255,255,0.018) 0 2px, rgba(0,0,0,0.05) 2px 5px),
      radial-gradient(ellipse at 50% 40%, var(--card-mid), var(--card-dark) 75%);
    box-shadow: 0 8px 22px rgba(0,0,0,0.28);
    overflow: hidden;
  }
  .card--front { top: 28px; }
  .card--back { top: 543px; }

  /* front */
  .brand {
    position: absolute;
    left: 70px;
    top: 140px;
    display: flex;
    align-items: center;
    gap: 22px;
  }
  .brand__dot {
    width: 64px;
    height: 64px;
    border-radius: 50%;
    background: var(--accent-teal);
  }
  .brand__name {
    font-weight: 700;
    font-size: 66px;
    letter-spacing: 6px;
    color: var(--brand-blue);
  }
  .band-rule {
    position: absolute;
    left: 0;
    width: 100%;
    height: 3px;
    background: var(--rule);
  }
  .band-rule--top { top: 240px; }
  .band-rule--bottom { top: 314px; }
  .band {
    position: absolute;
    left: 0;
    top: 250px;
    width: 100%;
    height: 56px;
    background: var(--band);
  }
  .band__person {
    position: absolute;
    left: 245px;
    top: 8px;
    font-size: 34px;
    font-weight: 700;
    color: var(--brand-blue);
    white-space: nowrap;
  }
  .band__title {
    font-weight: 500;
    font-size: 26px;
  }
  .details {
    position: absolute;
    top: 338px;
    left: 0;
    width: 100%;
    display: flex;
    justify-content: center;
    color: var(--text-light);
    font-size: 20px;
    line-height: 30px;
    font-weight: 500;
  }
  .details__address {
    text-align: right;
    padding-right: 24px;
    border-right: 2px solid var(--divider);
    padding-top: 18px;
  }
  .details__contact {
    list-style: none;
    margin: 0;
    padding: 0 0 0 24px;
  }
  .details__contact li {
    display: flex;
    align-items: center;
    gap: 10px;
  }
  .details__contact svg {
    width: 16px;
    height: 16px;
    flex: none;
  }

  /* back */
  .back-brand {
    position: absolute;
    left: 0;
    top: 150px;
    width: 100%;
    display: flex;
    justify-content: center;
    align-items: center;
    gap: 28px;
  }
  .back-brand__dot {
    width: 96px;
    height: 96px;
    border-radius: 50%;
    background: var(--accent-teal);
  }
  .back-brand__name {
    font-weight: 700;
    font-size: 84px;
    letter-spacing: 8px;
    color: var(--brand-blue);
  }
  .back-web {
    position: absolute;
    left: 0;
    top: 350px;
    width: 100%;
    text-align: center;
    font-size: 34px;
    font-weight: 500;
    letter-spacing: 9px;
    color: var(--band);
  }
</style>
</head>
<body>
<main class="sheet">
  <section class="card card--front" aria-label="Business card front">
    <div class="brand">
      <span class="brand__dot"></span>
      <span class="brand__name">VELUNDA</span>
    </div>
    <div class="band-rule band-rule--top"></div>
    <div class="band">
      <div class="band__person">Your Name, <span class="band__title">Title</span></div>
    </div>
    <div class="band-rule band-rule--bottom"></div>
    <div class="details">
      <address class="details__address" style="font-style:normal">
        Street Name<br>City Name<br>State, City Zip Code
      </address>
      <ul class="details__contact">
        <li>
          <svg viewBox="0 0 16 16"><circle cx="8" cy="8" r="7" fill="none" stroke="#f2f2f2" stroke-width="1.5"/><path d="M5 5c0 4 2 6 6 6l0-2-2-.5-1 1c-1-.5-2-1.5-2.5-2.5l1-1L6 5z" fill="#f2f2f2"/></svg>
          010-555-0142
        </li>
        <li>
          <svg viewBox="0 0 16 16"><circle cx="8" cy="8" r="7" fill="none" stroke="#f2f2f2" stroke-width="1.5"/><path d="M5 5c0 4 2 6 6 6l0-2-2-.5-1 1c-1-.5-2-1.5-2.5-2.5l1-1L6 5z" fill="#f2f2f2"/></svg>
          010-555-0142
        </li>
        <li>
          <svg viewBox="0 0 16 16"><rect x="1" y="4" width="14" height="9" fill="#f2f2f2"/><path d="M1 4l7 5 7-5" fill="none" stroke="#1b1b1d" stroke-width="1.2"/></svg>
          name@velunda.com
        </li>
        <li>
          <svg viewBox="0 0 16 16"><circle cx="8" cy="8" r="7" fill="none" stroke="#f2f2f2" stroke-width="1.4"/><ellipse cx="8" cy="8" rx="3" ry="7" fill="none" stroke="#f2f2f2" stroke-width="1.2"/><path d="M1 8h14" stroke="#f2f2f2" stroke-width="1.2"/></svg>
          www.velunda.com
        </li>
      </ul>
    </div>
  </section>

  <section class="card card--back" aria-label="Business card back">
    <div class="back-brand">
      <span class="back-brand__dot"></span>
      <span class="back-brand__name">VELUNDA</span>
    </div>
    <div class="back-web">www.velunda.com</div>
  </section>
</main>
</body>
</html>
```